Business Card Design

We need a business card designed for our new company. Prefer a black card with white logo & writing.

Contact Information for Business Card

Ted Galloway, address: 7-4812 Fernhollow Road, Abbotsford, BC, V3K 8R2, Office Phone: 604-712-3390, Cell: 604-947-2164, Email: ted@resinworkshub.ca

Colors

Designer to choose only greyscale colors for use in the design.

```html
<!DOCTYPE html>
<html lang="en">
<head>
<meta charset="UTF-8">
<title>Resin Works Hub – Business Card</title>
<link href="https://fonts.googleapis.com/css2?family=Poppins:wght@300;400;700;800&display=swap" rel="stylesheet">
<style>
  :root {
    --backdrop: #232325;
    --card: #1d1d1f;
    --ink: #ffffff;
    --ink-soft: #e6e6e6;
  }
  * { box-sizing: border-box; margin: 0; padding: 0; }
  html, body { width: 1200px; height: 780px; overflow: hidden; }
  body {
    background: var(--backdrop);
    font-family: "Poppins", sans-serif;
    color: var(--ink);
    position: relative;
  }
  .card {
    position: absolute;
    top: 247px;
    width: 500px;
    height: 286px;
    background: var(--card);
    box-shadow: 0 10px 30px rgba(0,0,0,0.45);
  }
  .card--contact { left: 60px; }
  .card--brand { left: 640px; }

  .brand-name {
    font-weight: 800;
    letter-spacing: 0.02em;
    text-transform: uppercase;
    line-height: 1;
    display: flex;
    align-items: center;
    gap: 8px;
    color: var(--ink);
  }
  .brand-name .brand-dot {
    width: 10px; height: 10px; border-radius: 50%;
    background: var(--ink);
    flex: none;
  }

  .card--contact .brand-name {
    position: absolute;
    top: 34px; right: 32px;
    font-size: 20px;
  }
  .contact-address {
    position: absolute;
    top: 82px; right: 32px;
    text-align: right;
    font-weight: 300;
    font-size: 12px;
    line-height: 1.45;
    color: var(--ink-soft);
  }
  .contact-list {
    position: absolute;
    top: 130px; right: 32px;
    list-style: none;
    font-weight: 300;
    font-size: 12px;
    color: var(--ink-soft);
  }
  .contact-list li {
    display: flex;
    justify-content: flex-end;
    align-items: center;
    gap: 8px;
    line-height: 1.45;
  }
  .contact-list .gap { margin-top: 10px; }
  .contact-list svg { width: 11px; height: 11px; flex: none; }

  .person {
    position: absolute;
    left: 32px; bottom: 32px;
  }
  .person-name {
    font-size: 24px;
    font-weight: 400;
    line-height: 1.1;
  }
  .person-name strong { font-weight: 700; }
  .person-title {
    font-size: 12px;
    font-weight: 300;
    margin-top: 4px;
    color: var(--ink-soft);
  }

  .card--brand .brand-name {
    position: absolute;
    left: 50%; top: 50%;
    transform: translate(-50%, -50%);
    font-size: 34px;
    white-space: nowrap;
  }
  .card--brand .brand-name .brand-dot { width: 16px; height: 16px; }
</style>
</head>
<body>

<section class="card card--contact" aria-label="Business card, contact side">
  <div class="brand-name"><span class="brand-dot"></span>Resin Works Hub</div>

  <p class="contact-address">7-4812 Fernhollow Road,<br>Abbotsford, BC, V3K 8R2.</p>

  <ul class="contact-list">
    <li>604-712-3390
      <svg viewBox="0 0 12 12" aria-hidden="true"><path d="M3 1 L5 3.5 L4 4.8 Q5.2 7 7.2 8 L8.5 7 L11 9 L9.8 10.8 Q5 10.5 1.2 2.2 Z" fill="#fff"/></svg>
    </li>
    <li>604-947-2164
      <svg viewBox="0 0 12 12" aria-hidden="true"><rect x="3" y="0.8" width="6" height="10.4" rx="1" fill="none" stroke="#fff" stroke-width="1.2"/><circle cx="6" cy="9.3" r="0.7" fill="#fff"/></svg>
    </li>
    <li class="gap">www.resinworkshub.ca
      <svg viewBox="0 0 12 12" aria-hidden="true"><circle cx="6" cy="6" r="5" fill="none" stroke="#fff" stroke-width="1.1"/><ellipse cx="6" cy="6" rx="2" ry="5" fill="none" stroke="#fff" stroke-width="0.9"/><line x1="1" y1="6" x2="11" y2="6" stroke="#fff" stroke-width="0.9"/></svg>
    </li>
    <li>ted@resinworkshub.ca
      <svg viewBox="0 0 12 12" aria-hidden="true"><rect x="1" y="2.5" width="10" height="7" fill="none" stroke="#fff" stroke-width="1.1"/><path d="M1 2.5 L6 6.5 L11 2.5" fill="none" stroke="#fff" stroke-width="1.1"/></svg>
    </li>
  </ul>

  <div class="person">
    <h1 class="person-name"><strong>Ted</strong> Galloway</h1>
    <p class="person-title">Founder &amp; CEO</p>
  </div>
</section>

<section class="card card--brand" aria-label="Business card, brand side">
  <div class="brand-name"><span class="brand-dot"></span>Resin Works Hub</div>
</section>

</body>
</html>
```